Larkfield Ridge Management

I need a professional website. My current website is larkfieldridgemanagement.com and I hate it. It was created with some AI tool very quickly because I needed a site up and running with no advanced notice. I’m open to all designs .. I trust you, the professionals will deliver the results I’m anxiously awaiting! :)

```html
<!DOCTYPE html>
<html lang="en">
<head>
<meta charset="utf-8">
<title>Larkfield Ridge Management</title>
<link href="https://fonts.googleapis.com/css2?family=Poppins:wght@400;500;600;700&display=swap" rel="stylesheet">
<style>
:root{
  --red:#b01c22;
  --red-deep:#9e151c;
  --navy:#1f2f57;
  --blue:#1f4e9c;
  --ink:#1d1d1d;
  --body:#3a3a3a;
  --ghost:#f1f1f1;
  --white:#ffffff;
  --field:#f7f7f7;
}
*{margin:0;padding:0;box-sizing:border-box}
html,body{width:1200px;height:4484px;overflow:hidden}
body{position:relative;background:var(--white);font-family:"Poppins",sans-serif;color:var(--ink)}
.abs{position:absolute}
a{text-decoration:none;color:inherit}

/* header */
.site-header{position:absolute;left:0;top:0;width:1200px;height:113px;background:var(--white);z-index:3}
.brand{position:absolute;left:60px;top:34px;display:flex;align-items:center;gap:12px}
.brand-mark{width:34px;height:34px;background:var(--red)}
.brand-name{font-weight:700;font-size:19px;color:var(--navy);line-height:1.15;width:200px}
.main-nav{position:absolute;top:48px;display:flex;font-size:13.5px;font-weight:500;color:var(--ink)}
.main-nav a{position:absolute;white-space:nowrap}
.main-nav .active{color:var(--red)}
.btn{position:absolute;display:flex;align-items:center;justify-content:center;border-radius:30px;color:var(--white);font-weight:600;text-transform:uppercase;white-space:nowrap}
.btn-red{background:var(--red)}
.btn-navy{background:var(--navy)}

/* hero */
.hero-edge{position:absolute;left:0;top:113px;width:1200px;height:630px}
.hero-photo{position:absolute;left:0;top:113px;width:1200px;height:616px;
  background:radial-gradient(circle at 52% 52%,#8d8a85 0,#6e6c68 22%,#4f4e4b 55%,#3a3a38 100%);
  clip-path:polygon(0 0,100% 0,100% 71%,50% 100%,0 71%)}
.hero-title{position:absolute;left:0;top:306px;width:1200px;text-align:center;color:var(--white);font-weight:700;font-size:47px;letter-spacing:-0.5px}
.hero-text{position:absolute;left:0;top:379px;width:1200px;text-align:center;color:var(--white);font-size:16.5px;line-height:26px}

/* section headings */
.ghost{position:absolute;font-weight:700;font-size:80px;color:var(--ghost);white-space:nowrap;line-height:1;letter-spacing:1px}
.section-title{position:absolute;font-size:41px;line-height:1;color:var(--red);white-space:nowrap}
.section-title strong{font-weight:700}
.section-title span{font-weight:400}

.hexagon{position:absolute;clip-path:polygon(50% 0,100% 25%,100% 75%,50% 100%,0 75%,0 25%)}

/* about */
.about-sub{position:absolute;left:64px;top:976px;font-size:20px;font-weight:600}
.about-copy{position:absolute;left:64px;width:476px;font-size:14px;line-height:25.3px;color:var(--body);text-align:justify}

/* services */
.service-card{position:absolute;width:516px;height:356px;background:var(--white);box-shadow:0 2px 8px rgba(0,0,0,.12)}
.service-card h3{height:68px;display:flex;align-items:center;justify-content:center;font-size:16px;font-weight:700;color:var(--blue);text-transform:uppercase;position:relative;z-index:1;background:var(--white)}
.service-card h3::after{content:"";position:absolute;left:50%;bottom:-13px;margin-left:-14px;border-left:14px solid transparent;border-right:14px solid transparent;border-top:14px solid var(--white)}
.service-photo{position:absolute;left:0;top:68px;width:516px;height:288px}

/* expertise band */
.band{position:absolute;left:0;top:2559px;width:1200px;height:482px;background:linear-gradient(180deg,#3b4f78 0%,#2f4570 45%,#2a3f63 100%)}
.band-title{position:absolute;left:0;top:2652px;width:1200px;text-align:center;color:var(--white);font-weight:700;font-size:62px;line-height:62px}
.band-text{position:absolute;left:0;top:2795px;width:1200px;text-align:center;color:var(--white);font-size:16.5px;line-height:26px}

/* contact form */
.contact-intro{position:absolute;left:64px;top:3333px;font-size:14px;color:var(--body)}
.field{position:absolute;background:var(--white);box-shadow:0 1px 6px rgba(0,0,0,.14);font-size:14px;color:#b5b5b5;padding:16px 12px}

/* footer */
.footer-shape{position:absolute;left:0;top:3870px;width:1200px;height:614px}
.footer-brand{position:absolute;left:120px;top:4178px;width:190px;text-align:center;font-weight:700;font-size:21px;line-height:1.2;color:var(--white)}
.social{position:absolute;width:36px;height:36px;border-radius:50%;background:var(--white)}
.footer-heading{position:absolute;top:4138px;font-size:23px;font-weight:600;color:var(--white)}
.footer-rule{position:absolute;top:4180px;width:60px;height:2px;background:rgba(255,255,255,.7)}
.footer-link{position:absolute;left:493px;font-size:13.5px;color:var(--white)}
.footer-link::before{content:"";position:absolute;left:-18px;top:7px;width:7px;height:7px;border-radius:50%;background:var(--white)}
.contact-icon{position:absolute;left:743px;width:36px;height:36px;border-radius:50%;background:var(--white);display:flex;align-items:center;justify-content:center}
.contact-line{position:absolute;left:791px;font-size:13.5px;line-height:21px;color:var(--white)}
.footer-divider{position:absolute;left:70px;top:4403px;width:1062px;height:1px;background:rgba(255,255,255,.45)}
.copyright{position:absolute;left:0;top:4437px;width:1200px;text-align:center;font-size:14px;color:var(--white)}
</style>
</head>
<body>

<header class="site-header">
  <div class="brand"><span class="brand-mark"></span><span class="brand-name">Larkfield Ridge Management</span></div>
  <nav class="main-nav">
    <a class="active" style="left:704px">HOME</a>
    <a style="left:773px">ABOUT US</a>
    <a style="left:866px">SERVICES</a>
  </nav>
  <a class="btn btn-red" style="left:961px;top:33px;width:173px;height:51px;font-size:14px">Contact Us</a>
</header>

<section class="hero">
  <svg class="hero-edge" viewBox="0 0 1200 630" aria-hidden="true"><polygon points="0,0 1200,0 1200,453 600,629 0,453" fill="#c8262a"/></svg>
  <div class="hero-photo" role="img" aria-label="Sculpted ribbed stone sphere resting on a dark surface"></div>
  <h1 class="hero-title">A TRUE PARTNER, NOT JUST A VENDOR.</h1>
  <p class="hero-text">Drawing on decades of collective expertise, the team facilitates regulatory compliance,<br>cost efficiency, and proactive maintenance.</p>
  <a class="btn btn-red" style="left:521px;top:449px;width:162px;height:47px;font-size:14.5px">Contact Now</a>
</section>

<section class="about">
  <div class="ghost" style="left:62px;top:862px">WHO WE ARE</div>
  <h2 class="section-title" style="left:64px;top:925px"><strong>ABOUT</strong> <span>US</span></h2>
  <h3 class="about-sub">About Our Property Management Solutions</h3>
  <p class="about-copy" style="top:1010px">Our organization delivers comprehensive property management solutions that optimize asset performance and tenant satisfaction. By integrating advanced analytics with proven operational frameworks, our specialists ensure each property achieves sustained value appreciation.</p>
  <p class="about-copy" style="top:1162px">Drawing on decades of collective expertise, the team facilitates regulatory compliance, cost efficiency, and proactive maintenance. This disciplined approach enables owners to preserve capital, enhance occupancy rates, and demonstrate long-term resilience across diverse market conditions.</p>
  <a class="btn btn-navy" style="left:64px;top:1303px;width:128px;height:45px;font-size:13px">Read More</a>
  <div class="hexagon" style="left:686px;top:848px;width:446px;height:514px;background:linear-gradient(160deg,#cbc2b5 0%,#b7ab9b 50%,#9e9282 100%)" role="img" aria-label="Stack of wooden blocks topped with a stone slab"></div>
</section>

<section class="services">
  <div class="ghost" style="left:0;width:1200px;text-align:center;top:1488px">WHAT WE DO</div>
  <h2 class="section-title" style="left:0;width:1200px;text-align:center;top:1550px"><strong>OUR</strong> <span>SERVICES</span></h2>

  <article class="service-card" style="left:77px;top:1637px">
    <h3>Basic Service</h3>
    <div class="service-photo" role="img" aria-label="Hands arranging material samples on a wooden table" style="background:linear-gradient(135deg,#9a7c5c 0%,#cfae86 45%,#e2c9a6 100%)"></div>
  </article>
  <article class="service-card" style="left:606px;top:1637px">
    <h3>Intermediate Service</h3>
    <div class="service-photo" role="img" aria-label="Modern bathroom vanity with sink and round mirror" style="background:linear-gradient(135deg,#6f655b 0%,#a89e92 50%,#cdbfae 100%)"></div>
  </article>
  <article class="service-card" style="left:77px;top:2017px">
    <h3>Advanced Service</h3>
    <div class="service-photo" role="img" aria-label="Desk with laptop, lamp and flowers in a vase" style="background:linear-gradient(135deg,#5c4a3a 0%,#b49c80 50%,#e4d6c4 100%)"></div>
  </article>
  <article class="service-card" style="left:606px;top:2017px">
    <h3>Advanced+ Service</h3>
    <div class="service-photo" role="img" aria-label="Globe lamp, bowl and brochure on a dark counter" style="background:linear-gradient(180deg,#d8c7b0 0%,#cdb89c 72%,#2a2420 86%,#1f1a17 100%)"></div>
  </article>
</section>

<section>
  <div class="band" role="img" aria-label="Aerial view of a tree-lined suburban neighbourhood with a city skyline, under a navy tint"></div>
  <h2 class="band-title">EXPERTISE ROOTED<br>IN ASSET PRESERVATION</h2>
  <p class="band-text">The organization applies rigorously tested frameworks and data-driven<br>methodologies to safeguard property value while elevating tenant experience.</p>
  <a class="btn btn-red" style="left:503px;top:2882px;width:194px;height:49px;font-size:14.5px">Learn More</a>
</section>

<section class="contact">
  <div class="ghost" style="left:62px;top:3218px">GET IN TOUCH</div>
  <h2 class="section-title" style="left:68px;top:3280px"><strong>CONTACT</strong> <span>US</span></h2>
  <p class="contact-intro">For more information,Please fill out the following and we will be in touch shortly</p>
  <div class="field" style="left:66px;top:3386px;width:261px;height:52px">First Name</div>
  <div class="field" style="left:350px;top:3386px;width:261px;height:52px">Second Name</div>
  <div class="field" style="left:66px;top:3466px;width:261px;height:52px">Phone</div>
  <div class="field" style="left:350px;top:3466px;width:261px;height:52px">Subject</div>
  <div class="field" style="left:66px;top:3541px;width:545px;height:99px">Message</div>
  <a class="btn btn-navy" style="left:66px;top:3673px;width:176px;height:44px;font-size:12.5px">Submit A Message</a>
  <div class="hexagon" style="left:686px;top:3210px;width:446px;height:514px;background:radial-gradient(circle at 50% 60%,#c79b72 0%,#8e7561 40%,#6f6358 100%)" role="img" aria-label="Architectural model of a modern house on a white base"></div>
</section>

<footer>
  <svg class="footer-shape" viewBox="0 0 1200 614" aria-hidden="true">
    <polygon points="0,180 600,4 1200,180 1200,614 0,614" fill="var(--navy)"/>
    <polygon points="0,196 600,24 1200,196 1200,614 0,614" fill="var(--red-deep)"/>
  </svg>
  <div class="footer-brand">Larkfield Ridge Management</div>
  <span class="social" style="left:140px;top:4307px"></span>
  <span class="social" style="left:189px;top:4307px"></span>
  <span class="social" style="left:236px;top:4307px"></span>

  <h4 class="footer-heading" style="left:470px">LINKS</h4>
  <span class="footer-rule" style="left:470px"></span>
  <a class="footer-link" style="top:4210px">About Us</a>
  <a class="footer-link" style="top:4242px">Services</a>
  <a class="footer-link" style="top:4275px">Contact</a>

  <h4 class="footer-heading" style="left:740px">CONTACT</h4>
  <span class="footer-rule" style="left:740px"></span>
  <span class="contact-icon" style="top:4209px"><svg width="16" height="18" viewBox="0 0 16 18"><path d="M8 0a6 6 0 0 0-6 6c0 4.5 6 12 6 12s6-7.5 6-12a6 6 0 0 0-6-6zm0 8.3A2.3 2.3 0 1 1 8 3.7a2.3 2.3 0 0 1 0 4.6z" fill="var(--red-deep)"/></svg></span>
  <p class="contact-line" style="top:4203px">Lorem ipsum,Lorem ipsum.<br>Lorem ipsum</p>
  <span class="contact-icon" style="top:4267px"><svg width="16" height="16" viewBox="0 0 16 16"><path d="M3.5 1l2.6 3-1.5 1.8a9 9 0 0 0 5.6 5.6L12 9.9l3 2.6-1.4 2.3C7 15 1 9 1.2 2.4z" fill="var(--red-deep)"/></svg></span>
  <p class="contact-line" style="top:4275px">(555) 014 2730</p>
  <span class="contact-icon" style="top:4322px"><svg width="17" height="12" viewBox="0 0 17 12"><rect width="17" height="12" rx="1.5" fill="var(--red-deep)"/><path d="M1 1.5l7.5 5.5L16 1.5" stroke="#fff" stroke-width="1.4" fill="none"/></svg></span>
  <p class="contact-line" style="top:4330px">info@larkfieldridgemanagement.com</p>

  <div class="footer-divider"></div>
  <p class="copyright">Copyright © 2026 All Rights Reserved By Company Name</p>
</footer>

</body>
</html>
```